Looking for a modern, Professional business card design

We have a simple business card, but are looking for a more modern, professional look. A sample of the basic card is attached as well as the logo. We would also like to add that we offer:
Struggling with your finances?
- Learn to become debt free
- Discover the power of cash
- Control your money instead of it controlling you
Let us help you achieve a new level of financial freedom!
Also, we would like to have a "SPECIAL OFFER!: FREE 30 minute consultation"
Financial Planning

```html
<!DOCTYPE html>
<html lang="en">
<head>
<meta charset="utf-8">
<title>Horizon Money Coaching – Business Card</title>
<link href="https://fonts.googleapis.com/css2?family=Open+Sans:wght@400;600;700;800&display=swap" rel="stylesheet">
<style>
  :root {
    --canvas: #ececea;
    --green-deep: #2f8a2a;
    --green: #4fa83a;
    --green-light: #a6d65a;
    --lime: #c8e86c;
    --white: #ffffff;
    --ink: #222222;
    --text-on-green: #ffffff;
    --band-text: #f2fbe8;
  }
  * { box-sizing: border-box; margin: 0; padding: 0; }
  html, body { width: 1200px; height: 843px; overflow: hidden; }
  body {
    background: var(--canvas);
    font-family: "Open Sans", Arial, sans-serif;
    display: flex;
    align-items: center;
    justify-content: center;
    gap: 48px;
  }
  .card {
    width: 540px;
    height: 309px;
    border-radius: 22px;
    overflow: hidden;
    position: relative;
    box-shadow: 0 10px 28px rgba(0,0,0,.22);
  }

  /* Back side */
  .card-back {
    background:
      radial-gradient(ellipse 55% 70% at 45% 45%, var(--lime) 0%, var(--green-light) 30%, transparent 75%),
      linear-gradient(180deg, var(--green) 0%, var(--green-deep) 100%);
    color: var(--text-on-green);
    text-align: right;
    padding: 26px 30px 0 30px;
  }
  .offer-heading {
    font-weight: 700;
    font-size: 15px;
    letter-spacing: .3px;
    text-transform: uppercase;
  }
  .benefit-list { list-style: none; margin-top: 4px; }
  .benefit-list li {
    font-size: 14px;
    line-height: 1.35;
  }
  .benefit-list li::after {
    content: "";
    display: inline-block;
    width: 7px; height: 7px;
    border-radius: 50%;
    background: var(--white);
    margin-left: 8px;
    vertical-align: middle;
  }
  .closing-line { font-size: 14px; line-height: 1.35; margin-top: 2px; }
  .special-offer {
    font-weight: 700;
    font-size: 17px;
    text-transform: uppercase;
    margin-top: 10px;
  }
  .special-detail { font-size: 13px; }
  .back-brand {
    margin-top: 8px;
    font-weight: 800;
    font-size: 30px;
    line-height: 1;
    color: var(--white);
    text-transform: uppercase;
  }
  .back-tagline { font-size: 11px; margin-top: 4px; opacity: .9; }

  /* Front side */
  .card-front { background: var(--white); }
  .brand-block {
    position: absolute;
    top: 56px;
    left: 150px;
    display: flex;
    align-items: center;
    gap: 14px;
  }
  .brand-mark {
    width: 34px; height: 34px;
    border-radius: 50%;
    background: var(--green);
    flex: none;
  }
  .brand-name {
    font-weight: 800;
    font-size: 30px;
    line-height: 1.05;
    color: var(--ink);
    text-transform: uppercase;
  }
  .brand-tagline {
    position: absolute;
    top: 136px;
    left: 198px;
    font-size: 11px;
    color: var(--ink);
    font-style: italic;
  }
  .contact-band {
    position: absolute;
    left: 0; right: 0; bottom: 0;
    height: 140px;
    background: linear-gradient(90deg, var(--green-light) 0%, var(--green) 45%, var(--green-deep) 100%);
    color: var(--band-text);
    padding: 18px 28px 0 40px;
  }
  .person-line { font-size: 18px; }
  .person-name { font-weight: 700; }
  .person-role { margin-left: 14px; }
  .contact-row {
    display: flex;
    gap: 26px;
    margin-top: 10px;
    font-size: 14px;
  }
  .contact-item { display: flex; align-items: center; gap: 7px; }
  .contact-item svg { width: 15px; height: 15px; flex: none; }
  .contact-web { margin-top: 8px; }
</style>
</head>
<body>

  <section class="card card-back" aria-label="Card back">
    <h2 class="offer-heading">Struggling with your finances?</h2>
    <ul class="benefit-list">
      <li>Learn to become debt free</li>
      <li>Discover the power of cash</li>
      <li>Control your money instead of it controlling you</li>
    </ul>
    <p class="closing-line">Let us help you achieve a new level of financial freedom!</p>
    <p class="special-offer">Special offer!</p>
    <p class="special-detail">FREE 30 minute consultation</p>
    <p class="back-brand">Horizon Money Coaching</p>
    <p class="back-tagline">Achieve a new level of personal freedom</p>
  </section>

  <section class="card card-front" aria-label="Card front">
    <div class="brand-block">
      <span class="brand-mark"></span>
      <span class="brand-name">Horizon<br>Money Coaching</span>
    </div>
    <p class="brand-tagline">Achieve a new level of personal freedom</p>

    <div class="contact-band">
      <p class="person-line"><span class="person-name">Daniel R. Hayes</span><span class="person-role">- &nbsp;Personal Financial Coach</span></p>
      <div class="contact-row">
        <span class="contact-item">
          <svg viewBox="0 0 16 16" aria-hidden="true"><rect x="4" y="1" width="8" height="14" rx="1.5" fill="none" stroke="currentColor" stroke-width="1.5"/><circle cx="8" cy="12.5" r=".9" fill="currentColor"/></svg>
          (555) 014-2290
        </span>
        <span class="contact-item">
          <svg viewBox="0 0 16 16" aria-hidden="true"><rect x="1" y="3" width="14" height="10" rx="1" fill="currentColor"/><path d="M1.5 3.5 8 9l6.5-5.5" fill="none" stroke="#3a9330" stroke-width="1.3"/></svg>
          daniel@steadymoneypath.com
        </span>
      </div>
      <div class="contact-row contact-web">
        <span class="contact-item">
          <svg viewBox="0 0 16 16" aria-hidden="true"><circle cx="8" cy="8" r="6.5" fill="none" stroke="currentColor" stroke-width="1.4"/><ellipse cx="8" cy="8" rx="2.8" ry="6.5" fill="none" stroke="currentColor" stroke-width="1.1"/><path d="M1.5 8h13" stroke="currentColor" stroke-width="1.1"/></svg>
          www.steadymoneypath.com
        </span>
      </div>
    </div>
  </section>

</body>
</html>
```